Specialised investor in e-mobility and energy wants business card design

We need a business card design that fits our existing corporate design. <The look and feel must be 'sharp'/'clean', dynamic, communicate momentum, professionalism etc (as one would imagine from a firm in the financial sector). We like the idea of a reverse-side of the card that includes the logo, and the name and contact details on the other. We expect the deliverable to be whatever format might be required to be able to get cards printed directly by a service such as kelmo press. Our website is www.zub.capital

```html
<!DOCTYPE html>
<html lang="en">
<head>
<meta charset="utf-8">
<title>Zub Capital – Business Card</title>
<link href="https://fonts.googleapis.com/css2?family=Montserrat:wght@300;400;500;700&display=swap" rel="stylesheet">
<style>
  :root {
    --bg: #d8d8d6;
    --green-dark: #33502a;
    --green-deep: #2b4522;
    --green-light: #7ab342;
    --swoosh: #eef3e8;
    --white: #ffffff;
    --ink: #3a3a3a;
  }
  * { margin: 0; padding: 0; box-sizing: border-box; }
  html, body { width: 1200px; height: 801px; overflow: hidden; }
  body {
    background: var(--bg);
    font-family: 'Montserrat', sans-serif;
    position: relative;
  }
  .card {
    position: absolute;
    top: 246px;
    width: 540px;
    height: 309px;
    overflow: hidden;
    box-shadow: 0 6px 18px rgba(0,0,0,0.18);
  }
  .card-front { left: 40px; background: var(--white); }
  .card-back { left: 620px; background: var(--green-dark); }

  .brand-band {
    position: absolute; left: 0; top: 0; bottom: 0;
    width: 120px;
    background: var(--green-dark);
  }
  .brand-band .brand-name {
    position: absolute; left: 50%; top: 50%;
    transform: translate(-50%, -50%) rotate(90deg);
    white-space: nowrap;
    color: var(--white);
    font-weight: 300;
    font-size: 34px;
    letter-spacing: 1px;
  }
  .swoosh { position: absolute; left: 120px; top: 0; width: 420px; height: 309px; }

  .details { position: absolute; left: 150px; top: 78px; color: var(--ink); }
  .person-name {
    font-weight: 700; font-size: 23px; letter-spacing: 1px; line-height: 1;
    color: var(--green-dark);
  }
  .person-name .surname { color: var(--green-light); }
  .person-role { font-size: 13px; margin-top: 5px; font-weight: 400; }
  .contact-list { list-style: none; margin-top: 16px; font-size: 13px; line-height: 21px; }
  .contact-list li { display: flex; align-items: center; gap: 8px; }
  .contact-list svg { width: 10px; height: 10px; flex: none; }
  .address { margin-top: 16px; font-size: 13px; line-height: 18px; }

  .monogram-field {
    position: absolute; inset: 0;
    background: linear-gradient(135deg, #2f4a26 0%, #3b5a2f 55%, #456a35 100%);
  }
  .back-mark {
    position: absolute; right: 80px; bottom: 96px;
    color: var(--white);
    font-weight: 700; font-size: 30px; letter-spacing: 2px;
  }
</style>
</head>
<body>
  <section class="card card-front">
    <div class="brand-band"><span class="brand-name">Zub capital</span></div>
    <svg class="swoosh" viewBox="0 0 420 309" aria-hidden="true">
      <path d="M 30 309 C 110 160, 250 50, 420 10 L 420 0 C 240 40, 90 150, 14 309 Z" fill="var(--swoosh)"/>
    </svg>
    <div class="details">
      <h1 class="person-name">MARTEN <span class="surname">SOLBERG</span></h1>
      <p class="person-role">Director/Founder</p>
      <ul class="contact-list">
        <li><svg viewBox="0 0 10 10"><path d="M2 1 L4 1 L4.6 3 L3.4 3.8 Q4.5 5.8 6.2 6.6 L7 5.4 L9 6 L9 8 Q5 9 2.5 6 Q1 4 2 1 Z" fill="var(--green-light)"/></svg>123-480-2917</li>
        <li><svg viewBox="0 0 10 10"><rect x="0.5" y="2" width="9" height="6.5" fill="var(--green-light)"/><path d="M0.5 2 L5 5.5 L9.5 2" stroke="var(--white)" stroke-width="0.8" fill="none"/></svg>info@zub.capital</li>
        <li><svg viewBox="0 0 10 10"><circle cx="5" cy="5" r="4.5" fill="var(--green-light)"/><path d="M0.5 5 H9.5 M5 0.5 V9.5" stroke="var(--white)" stroke-width="0.7"/></svg>www.zub.capital</li>
      </ul>
      <p class="address">1234 Street Name<br>Country Name AB 5748</p>
    </div>
  </section>

  <section class="card card-back">
    <div class="monogram-field" role="img" aria-label="Embossed repeating brand monogram pattern in dark green tones"></div>
    <span class="back-mark">ZUB</span>
  </section>
</body>
</html>
```